High-end construction company needs a business card design

We need a modern looking business card that draws people in, is memorable and looks so good people will want to sick it on their fridges.
On the first side what is needed are:
Logo
My name - Tomasz Brelwik
Title - Managing Director
Website - www.varkelt.co.uk
Email - tomasz@varkelt.co.uk
Telephone - 020 5194 6281
Mobile - 07845139072
On the back side was is needed is a list of all the services we provide:
-Kitchen Renovations
-Bathroom Renovations
-House Renovations
-Garage Conversions
-Extensions
-Loft Conversions
-Conservatories
-Carpentry
-Tiling
-Electrical
-Plumbing & Heating
-Bricklaying
-Landscaping
-Decorating
-Plastering
We would like the colours to be the same shades as on the logo with grey or black for the words.
Target Market(s)
Anyone who needs building work done
Contact Information for Business Card
This business card is for a construction company which strives to deliver excellent service and quality.
The look and feel of the card should represent this.
Requirements
Must have
- On the first side what is needed are:
Logo
My name - Tomasz Brelwik
Title - Managing Director
Website - www.varkelt.co.uk
Email - tomasz@varkelt.co.uk
Telephone - 020 5194 6281
Mobile - 07845139072
Nice to have
- Cool looking features

```html
<!DOCTYPE html>
<html lang="en">
<head>
<meta charset="utf-8">
<title>Varkelt Construction Ltd – Business Card</title>
<link href="https://fonts.googleapis.com/css2?family=Montserrat:wght@400;700;800&family=Questrial&display=swap" rel="stylesheet">
<style>
  :root {
    --bg: #e4e4e4;
    --green-dark: #3f8a3a;
    --green-mid: #5a9e4f;
    --green-light: #79b06c;
    --green-brand: #6cbb45;
    --green-accent: #80c453;
    --green-icon: #9bd07c;
    --green-tick: #3e9a34;
    --white: #ffffff;
    --text-grey: #4d4d4d;
  }
  * { box-sizing: border-box; margin: 0; padding: 0; }
  html, body { width: 1200px; height: 1200px; overflow: hidden; }
  body { background: var(--bg); position: relative; }

  .card {
    position: absolute;
    left: 257px;
    width: 686px;
    height: 392px;
  }
  .card--front {
    top: 165px;
    background: linear-gradient(200deg, var(--green-light) 0%, var(--green-mid) 45%, var(--green-dark) 100%);
  }
  .card--back {
    top: 653px;
    background: var(--white);
  }

  /* Front */
  .identity {
    position: absolute;
    right: 346px;
    top: 170px;
    text-align: right;
    font-family: "Montserrat", sans-serif;
  }
  .identity__name {
    font-weight: 800;
    font-size: 27px;
    letter-spacing: 0.5px;
    color: var(--green-accent);
    text-transform: uppercase;
    line-height: 1;
  }
  .identity__title {
    margin-top: 4px;
    font-weight: 700;
    font-size: 12.5px;
    color: var(--white);
    text-transform: uppercase;
    letter-spacing: -0.2px;
  }
  .divider {
    position: absolute;
    left: 366px;
    top: 156px;
    width: 1px;
    height: 80px;
    background: var(--green-accent);
    opacity: 0.8;
  }
  .contacts {
    position: absolute;
    left: 389px;
    top: 155px;
    list-style: none;
    font-family: "Montserrat", sans-serif;
    font-size: 15.5px;
    color: var(--white);
  }
  .contacts li {
    display: flex;
    align-items: center;
    height: 20.7px;
  }
  .contacts svg {
    width: 12px;
    height: 12px;
    margin-right: 10px;
    fill: var(--green-icon);
    flex: none;
  }

  /* Back */
  .brand {
    position: absolute;
    top: 112px;
    left: 0;
    width: 100%;
    display: flex;
    justify-content: center;
    align-items: center;
    gap: 12px;
    font-family: "Montserrat", sans-serif;
    font-weight: 800;
    color: var(--green-brand);
  }
  .brand__mark {
    width: 26px;
    height: 26px;
    background: var(--green-brand);
  }
  .brand__name {
    font-size: 44px;
    letter-spacing: 1px;
    line-height: 1;
  }
  .brand__sub {
    position: absolute;
    top: 170px;
    width: 100%;
    text-align: center;
    font-family: "Montserrat", sans-serif;
    font-weight: 800;
    font-size: 14px;
    letter-spacing: 3px;
    color: var(--green-brand);
  }
  .services {
    position: absolute;
    top: 233px;
    width: 100%;
    font-family: "Questrial", sans-serif;
    font-size: 15px;
    color: var(--text-grey);
    text-align: center;
    line-height: 21.5px;
  }
  .services__row { white-space: nowrap; }
  .tick {
    display: inline-block;
    width: 12px;
    height: 12px;
    vertical-align: -1px;
    margin: 0 3px;
  }
  .social {
    position: absolute;
    top: 334px;
    width: 100%;
    display: flex;
    justify-content: center;
    gap: 5px;
  }
  .social__item {
    width: 21px;
    height: 21px;
    border: 1.6px solid var(--green-tick);
    border-radius: 5px;
  }
</style>
</head>
<body>

<svg width="0" height="0" style="position:absolute">
  <defs>
    <symbol id="tick-box" viewBox="0 0 12 12">
      <rect x="0.75" y="0.75" width="10.5" height="10.5" fill="none" stroke="#3e9a34" stroke-width="1.5"/>
      <path d="M3 6.2 L5.2 8.3 L9.2 3.6" fill="none" stroke="#3e9a34" stroke-width="1.6"/>
    </symbol>
  </defs>
</svg>

<section class="card card--front" aria-label="Business card front">
  <div class="identity">
    <p class="identity__name">Tomasz Brelwik</p>
    <p class="identity__title">Managing Director</p>
  </div>
  <div class="divider"></div>
  <ul class="contacts">
    <li>
      <svg viewBox="0 0 12 12"><path d="M2.5 0.8 L4.3 0.5 L5.2 3.2 L4 4.2 C4.6 5.6 6.3 7.4 7.8 8 L8.8 6.8 L11.5 7.7 L11.2 9.5 C10.9 10.8 9.8 11.4 8.6 11 C5 9.8 2.2 7 1 3.4 C0.6 2.2 1.2 1.1 2.5 0.8 Z"/></svg>
      020 5194 6281
    </li>
    <li>
      <svg viewBox="0 0 12 12"><path d="M3 0 H9 V12 H3 Z M4.2 1.4 V9.2 H7.8 V1.4 Z M5.5 10 H6.5 V11 H5.5 Z" fill-rule="evenodd"/></svg>
      07845139072
    </li>
    <li>
      <svg viewBox="0 0 12 12"><path d="M0.5 2.5 H11.5 V9.5 H0.5 Z"/><path d="M0.8 2.8 L6 6.6 L11.2 2.8" fill="none" stroke="#5a9e4f" stroke-width="1"/></svg>
      tomasz@varkelt.co.uk
    </li>
    <li>
      <svg viewBox="0 0 12 12"><circle cx="6" cy="6" r="5.5"/><path d="M2.5 4 C4 3.5 5 5 4.5 6.5 C4 8 5.5 9 6.5 10.5 M7.5 1.5 C8 3 9.5 3.5 10.5 4" fill="none" stroke="#5a9e4f" stroke-width="1.1"/></svg>
      www.varkelt.co.uk
    </li>
  </ul>
</section>

<section class="card card--back" aria-label="Business card back">
  <div class="brand">
    <span class="brand__mark"></span>
    <span class="brand__name">VARKELT</span>
  </div>
  <p class="brand__sub">CONSTRUCTION LTD</p>

  <div class="services">
    <p class="services__row">Kitchen Renovations<svg class="tick"><use href="#tick-box"/></svg>Bathroom Renovations<svg class="tick"><use href="#tick-box"/></svg>House Renovations</p>
    <p class="services__row">Garage Conversions<svg class="tick"><use href="#tick-box"/></svg>Extensions<svg class="tick"><use href="#tick-box"/></svg>Loft Conversions<svg class="tick"><use href="#tick-box"/></svg>Conservatories</p>
    <p class="services__row">Carpentry<svg class="tick"><use href="#tick-box"/></svg>Tiling<svg class="tick"><use href="#tick-box"/></svg>Electrical<svg class="tick"><use href="#tick-box"/></svg>Plumbing &amp; Heating<svg class="tick"><use href="#tick-box"/></svg>Bricklaying</p>
    <p class="services__row">Landscaping<svg class="tick"><use href="#tick-box"/></svg>Decorating<svg class="tick"><use href="#tick-box"/></svg>Plastering</p>
  </div>

  <div class="social" aria-label="Social media links">
    <span class="social__item"></span>
    <span class="social__item"></span>
    <span class="social__item"></span>
  </div>
</section>

</body>
</html>
```